International Trade Consulting Firm Seeks Quality Newsletter Design

Our company provides consulting services to Pinnacle 300 type companies. We compete with the largest consulting companies in the world. However, we have the highest level of expertise in the industry and need to look the most professional and high end. We have very relevant and important information to provide our customers about their compliance and projects. We will have the winning design coded to be an e-newsletter, so it needs to be one page. We want to keep our company colors and logo design in the newsletter, they are attached. We DO NOT want it to look like a mini-version of our website. We want a fresh look to this marketing piece. Newsletter will need to include title, possible sub-heading, space for a feature story, 2 other stories included, and space on either the left or right for short cuts, links or highlights of other articles. Contents/'In this issue' section, about us or branding area, section for relevant links, etc...
Pinnacle 300 companies, High-level management
Marketing

```html
<!DOCTYPE html>
<html lang="en">
<head>
<meta charset="utf-8">
<title>Harborline Trade Corporation Newsletter – 04/14</title>
<link href="https://fonts.googleapis.com/css2?family=Open+Sans:ital,wght@0,400;0,600;0,700;1,700&family=PT+Sans:wght@400;700&display=swap" rel="stylesheet">
<style>
  :root {
    --page-top: #2c6cab;
    --page-bottom: #164578;
    --sheet: #ffffff;
    --ink: #333333;
    --muted: #777777;
    --bar-dark: #121212;
    --panel-dark: #1f2a36;
    --brand-green: #5aaa45;
    --hero-dark: #0f2a17;
    --hero-mid: #2f6e3c;
    --link-blue: #2b7bc0;
    --accent-orange: #f39a1e;
    --placeholder: #ececec;
    --rule: #dddddd;
  }
  * { box-sizing: border-box; margin: 0; padding: 0; }
  html, body { width: 763px; height: 1200px; overflow: hidden; }
  body {
    background: linear-gradient(180deg, var(--page-top), var(--page-bottom));
    font-family: "Open Sans", Verdana, sans-serif;
    color: var(--ink);
  }
  .preheader {
    height: 56px; padding-top: 10px;
    text-align: center; color: #fff; font-size: 8.5px; line-height: 13px;
  }
  .preheader a { color: #cfe4ff; }
  .sheet {
    width: 448px; margin: 0 auto; background: var(--sheet); padding: 8px;
  }
  .masthead {
    height: 46px; background: var(--bar-dark);
    display: flex; align-items: center; padding: 0 10px; gap: 10px;
  }
  .masthead__logo {
    font-family: "PT Sans", sans-serif; font-weight: 700; font-size: 20px;
    color: #fff; letter-spacing: 1px; display: flex; align-items: center; gap: 5px;
  }
  .masthead__logo span.mark { width: 10px; height: 10px; background: var(--brand-green); display: inline-block; }
  .masthead__tagline { flex: 1; text-align: right; color: #fff; font-size: 10.5px; font-weight: 600; }
  .masthead__social { width: 20px; height: 20px; background: var(--link-blue); border-radius: 2px; }
  .hero {
    position: relative; height: 170px; margin-top: 8px;
    background: radial-gradient(ellipse at 35% 40%, var(--hero-mid), var(--hero-dark) 75%);
  }
  .hero__title {
    position: absolute; left: 140px; top: 92px;
    font-family: "PT Sans", sans-serif; color: #fff; font-size: 18px; line-height: 22px;
  }
  .content { display: flex; gap: 12px; margin-top: 14px; }
  .feature { width: 268px; border: 1px solid var(--rule); padding: 10px; }
  .feature h2 { font-size: 11px; font-weight: 400; letter-spacing: .5px; color: var(--ink); margin-bottom: 10px; }
  .feature__lead { display: flex; gap: 8px; margin-bottom: 10px; }
  .feature__image { width: 118px; height: 112px; flex: none; }
  .copy { font-size: 8px; line-height: 11px; color: var(--muted); }
  .feature .copy + .copy { margin-top: 9px; }
  .sidebar { width: 152px; }
  .sidebar__head {
    background: var(--panel-dark); color: #fff; font-size: 11px; font-weight: 700; font-style: italic;
    height: 24px; line-height: 24px; padding-left: 8px;
  }
  .issue-list { list-style: none; padding: 8px 4px 10px; }
  .issue-list li { display: flex; gap: 6px; margin-bottom: 9px; font-size: 7.5px; line-height: 10px; color: var(--muted); }
  .issue-list svg { flex: none; }
  .about__media { width: 152px; height: 80px; margin-top: 8px;
    background: linear-gradient(135deg, #5b4a3a, #a88d6b 55%, #3b3027); position: relative; }
  .about__play { position: absolute; left: 58px; top: 22px; }
  .about__link { color: var(--accent-orange); font-weight: 700; font-size: 10.5px; line-height: 13px; margin-top: 5px; }
  .news-band { background: var(--brand-green); height: 228px; margin-top: 18px; display: flex; padding: 18px 14px; gap: 14px; }
  .news-band__side { width: 120px; }
  .news-band__side h3 { color: #fff; font-size: 11.5px; font-weight: 600; margin-bottom: 6px; }
  .news-band__photo { width: 120px; height: 150px; background: linear-gradient(160deg, #cfe3f5, #3d78b5 60%, #1b3f6b); }
  .news-list { list-style: none; flex: 1; padding-top: 22px; }
  .news-list li { display: flex; gap: 10px; margin-bottom: 18px; color: #fff; font-size: 8px; font-weight: 600; line-height: 11px; }
  .news-list svg { flex: none; }
  .clients { margin-top: 14px; }
  .clients h3 { font-size: 12px; font-weight: 400; color: var(--ink); margin-bottom: 12px; }
  .clients__row { display: flex; justify-content: space-around; align-items: center; height: 46px; border-bottom: 1px solid var(--rule); }
  .clients__name { font-size: 13px; font-weight: 700; color: var(--ink); }
  .footer { text-align: center; padding: 12px 20px 14px; font-size: 7.5px; line-height: 10px; color: var(--muted); }
  .footer a { color: var(--link-blue); }
  .footer__social { display: flex; justify-content: center; gap: 6px; margin: 8px 0; }
  .footer__social span { width: 16px; height: 16px; background: var(--link-blue); border-radius: 2px; }
</style>
</head>
<body>
  <div class="preheader">
    Some contents of this email may not display and / or behave properly.<br>
    Learn more...<br>
    If you are unable to see the message below, click <a href="#">here</a> to view.
  </div>

  <main class="sheet">
    <header class="masthead">
      <div class="masthead__logo"><span class="mark"></span>HTCO</div>
      <div class="masthead__tagline">From the Leading Providers of Foreign-Trade Zones</div>
      <div class="masthead__social" aria-label="Professional network"></div>
    </header>

    <section class="hero" role="img" aria-label="Green world map backdrop">
      <h1 class="hero__title">Harborline Trade Corporation<br>Newsletter - 04/14</h1>
    </section>

    <div class="content">
      <article class="feature">
        <h2>LOREM IPSUM DOLOR SIT AMET</h2>
        <div class="feature__lead">
          <svg class="feature__image" viewBox="0 0 118 112" role="img" aria-label="Feature story image">
            <rect width="118" height="112" fill="var(--placeholder)"/>
            <path d="M0 0 L118 112 M118 0 L0 112" stroke="#d6d6d6" stroke-width="1.5"/>
          </svg>
          <div>
            <p class="copy">Lorem ipsum dolor sit amet, consectetur adipisicing elit, sed do eiusmod tempor incididunt ut labore et dolore magna aliqua.</p>
            <p class="copy" style="margin-top:9px">velit esse cillum dolore eu fugiat nulla pariatur. Excepteur sint occaecat.</p>
          </div>
        </div>
        <p class="copy">Lorem ipsum dolor sit amet, consectetur adipisicing elit, sed do eiusmod tempor incididunt ut labore et dolore magna aliqua.</p>
        <p class="copy">velit esse cillum dolore eu fugiat nulla pariatur. Excepteur sint occaecat cupidatat non proident, sunt in culpa qui officia deserunt mollit anim id est laborum. Lorem ipsum dolor sit amet, consectetur adipisicing elit, sed do eiusmod tempor incididunt ut labore et dolore magna aliqua.</p>
        <p class="copy">velit esse cillum dolore eu fugiat nulla pariatur. Excepteur sint occaecat cupidatat non proident, sunt in culpa qui officia deserunt mollit anim id est laborum.</p>
      </article>

      <aside class="sidebar">
        <div class="sidebar__head">In this Issue</div>
        <ul class="issue-list">
          <li><svg width="14" height="14" viewBox="0 0 14 14"><circle cx="7" cy="7" r="6" fill="none" stroke="#999"/><path d="M6 4.5 L8.5 7 L6 9.5" fill="none" stroke="#999" stroke-width="1.4"/></svg>Lorem ipsum dolor sit amet, consectetur adipisicing elit, sed do eiusmod tempor.</li>
          <li><svg width="14" height="14" viewBox="0 0 14 14"><circle cx="7" cy="7" r="6" fill="none" stroke="#999"/><path d="M6 4.5 L8.5 7 L6 9.5" fill="none" stroke="#999" stroke-width="1.4"/></svg>sed do eiusmod tempor incididunt ut labore et dolore.</li>
          <li><svg width="14" height="14" viewBox="0 0 14 14"><circle cx="7" cy="7" r="6" fill="none" stroke="#999"/><path d="M6 4.5 L8.5 7 L6 9.5" fill="none" stroke="#999" stroke-width="1.4"/></svg>Lorem ipsum dolor sit amet, consectetur adipisicing elit.</li>
        </ul>
        <div class="sidebar__head">About Us</div>
        <div class="about__media" role="img" aria-label="Company profile video still">
          <svg class="about__play" width="36" height="36" viewBox="0 0 36 36"><circle cx="18" cy="18" r="16" fill="rgba(255,255,255,.75)"/><path d="M14 11 L25 18 L14 25 Z" fill="#333"/></svg>
        </div>
        <p class="about__link">View our Company<br>profile media</p>
      </aside>
    </div>

    <section class="news-band">
      <div class="news-band__side">
        <h3>More Harborline News</h3>
        <div class="news-band__photo" role="img" aria-label="Office tower against the sky"></div>
      </div>
      <ul class="news-list">
        <li><svg width="22" height="22" viewBox="0 0 22 22"><circle cx="11" cy="11" r="10" fill="none" stroke="#fff" stroke-width="1.5"/><path d="M9 6.5 L13.5 11 L9 15.5" fill="none" stroke="#fff" stroke-width="2"/></svg>Lorem ipsum dolor sit amet, consectetur adipisicing elit, sed do eiusmod tempor incididunt ut labore et dolore magna aliqua.</li>
        <li><svg width="22" height="22" viewBox="0 0 22 22"><circle cx="11" cy="11" r="10" fill="none" stroke="#fff" stroke-width="1.5"/><path d="M9 6.5 L13.5 11 L9 15.5" fill="none" stroke="#fff" stroke-width="2"/></svg>Lorem ipsum dolor sit amet, consectetur adipisicing elit, sed do eiusmod tempor.</li>
        <li><svg width="22" height="22" viewBox="0 0 22 22"><circle cx="11" cy="11" r="10" fill="none" stroke="#fff" stroke-width="1.5"/><path d="M9 6.5 L13.5 11 L9 15.5" fill="none" stroke="#fff" stroke-width="2"/></svg>Lorem ipsum dolor sit amet, consectetur adipisicing elit, sed do eiusmod tempor.</li>
      </ul>
    </section>

    <section class="clients">
      <h3>From our Clients List...</h3>
      <div class="clients__row">
        <span class="clients__name">Arvent</span>
        <span class="clients__name">Coastal Keel</span>
        <span class="clients__name">Brightmast</span>
        <span class="clients__name">Cavenor</span>
      </div>
    </section>

    <footer class="footer">
      <p>You are receiving this email because you subscribed for our newsletter. To stop receiving it please <a href="#">unsubscribe here</a>. Having trouble reading this email? <a href="#">View it in your browser</a>.</p>
      <div class="footer__social" aria-label="Social links"><span></span><span></span></div>
      <p>Harborline Trade Corporation · 120 Meridian Way, Suite 400, Portvale · (555) 014-2290</p>
    </footer>
  </main>
</body>
</html>
```